KVT Web Design Project

I would like a simple and elegant design for my international business consulting practice web site. I already have new KVT Logo and will have brochure-colors are blue, green and black

Practice areas:
I offer consulting services specializing in developing Internet-based anti-counterfeiting and anti-fraud programs, test purchases and investigations.

I offer Cyber Security, Data Protection and Compliance services

I also offer International Due Diligence Investigations and Country and Travel Risk Assessments

General Background Investigations

Physical Security Services

About me section listing my Bio

I have a set of key associates that I work with around the world and will want to list their CVs or Bios under "KVT

Associates"Banner with nice photo but not too cluttered

Ability to Upload documents and articles

Contact us section
Updates

I have uploaded my new logo-please advise if you didn't get it or it is not in the correct file format.

Thank you

Dominic

Hello Everyone,

Thank you for your submissions and ideas. I'm not sure about design only vs code. I understand that some of you do not do code-if not then please just provide design.

More about my business: see below link on Google docs to my brochure-this should help but don't use that phone number-see below.

https://files.quillbin.example/view?id=7Qx2Lm9Pz4Rt8Kw3Hn6Vb1Jc5Fd0Sg

 

Here are some details.

Contacts:

Dominic R. Torvello, CPP

President

Torvello and Associates, LLC

P.O. Box 47129

Gaithersburg, MD 20914

USA

web address:www.Torvelloandassociates.example (currently not working)

email:dom @torvelloand associates.example

Tel: 202-555-0173

I hope this is helpful. Dom

Reason: Sorry but during holiday period, have not had as much time to devote to this project. Thanks for your submissions.

Per my previous guidance, please keep designs simple and elegant and free from traditional security images with locks and chains-I prefer one or at most, two photos. Two colors- blue and green in addition to black for print. I want to present professional, corporate and international image. Thank you for your ideas nad submissions.

Dom

Target Market(s)

Law firms, large multi-national corporations, Security Industry

Industry/Entity Type

Business

Requirements
Must have
• Must have sections: (will provide text)

About KVT (will provide text)

Practice areas

Associates (will provide text)

Contact us

(it must also have ability to upload files and articles)
Should not have
• Old style fonts and symbols such as security badges, scales of justice, etc. I want a sleek and modern design.

```html
<!DOCTYPE html>
<html lang="en">
<head>
<meta charset="utf-8">
<title>KVT – Torvello &amp; Associates, LLC</title>
<link href="https://fonts.googleapis.com/css2?family=Arimo:wght@400;700&family=Open+Sans:wght@400&display=swap" rel="stylesheet">
<style>
  :root {
    --page-bg: #222222;
    --top-strip: #2b2b2b;
    --header-zone: #272727;
    --brand-blue: #1b67a8;
    --nav-top: #2f86c6;
    --nav-bottom: #0f5b98;
    --nav-active: #4b9ad3;
    --link-blue: #3c8fd0;
    --text-light: #d2d2d2;
    --text-muted: #bdbdbd;
    --heading: #e4e4e4;
    --ink: #262626;
    --white: #ffffff;
    --dot-dark: #1e1e1e;
    --footer-bg: #262626;
  }
  * { box-sizing: border-box; margin: 0; padding: 0; }
  html, body { width: 1123px; height: 1200px; overflow: hidden; }
  body {
    position: relative;
    background: var(--page-bg);
    font-family: "Arimo", Arial, sans-serif;
    color: var(--text-light);
  }
  .top-strip { position: absolute; left: 0; top: 0; width: 1123px; height: 25px; background: var(--top-strip); border-bottom: 1px solid #1a1a1a; }
  .header-zone { position: absolute; left: 0; top: 25px; width: 1123px; height: 162px; background: var(--header-zone); }

  .masthead {
    position: absolute; left: 88px; top: 34px; width: 942px; height: 93px;
    background: linear-gradient(#ffffff, #ececec);
  }
  .brand-mark { position: absolute; left: 34px; top: 16px; font-size: 33px; color: var(--brand-blue); letter-spacing: -1px; }
  .brand-name { position: absolute; left: 117px; top: 19px; font-family: "Open Sans", Arial, sans-serif; font-size: 27px; color: var(--ink); }
  .brand-tagline { position: absolute; left: 34px; top: 54px; font-family: "Open Sans", Arial, sans-serif; font-size: 17px; letter-spacing: 2.3px; color: var(--brand-blue); }
  .search-field {
    position: absolute; left: 702px; top: 29px; width: 143px; height: 27px;
    border: 1px solid #c9c9c9; border-radius: 4px; background: var(--white);
    font-size: 14px; color: #a8a8a8; padding: 5px 15px;
  }
  .search-go {
    position: absolute; left: 856px; top: 27px; width: 37px; height: 27px;
    border-radius: 4px; background: linear-gradient(#2a7fc2, #0d5894);
    color: var(--white); font-size: 12px; text-align: center; line-height: 26px;
  }

  .main-nav {
    position: absolute; left: 88px; top: 139px; width: 942px; height: 46px;
    background: linear-gradient(var(--nav-top), var(--nav-bottom));
  }
  .main-nav a {
    position: absolute; top: 0; height: 46px; line-height: 48px;
    color: var(--white); text-decoration: none; font-size: 14px;
  }
  .main-nav .is-active { left: 0; width: 104px; text-align: center; background: linear-gradient(var(--nav-active), #1c6aa8); }

  .hero-frame { position: absolute; left: 88px; top: 200px; width: 942px; height: 373px; background: var(--white); }
  .hero-photo {
    position: absolute; left: 7px; top: 7px; width: 928px; height: 334px;
    background: linear-gradient(180deg, #e8f0f6 0%, #b8cde0 55%, #6d5446 82%, #4a3a33 100%);
  }
  .hero-dots { position: absolute; left: 433px; top: 350px; display: flex; gap: 3px; }
  .hero-dots span { width: 18px; height: 18px; border-radius: 50%; background: var(--dot-dark); }
  .hero-dots .is-current { background: var(--brand-blue); }

  .service { position: absolute; top: 607px; width: 210px; }
  .service h2 { font-weight: 400; font-size: 13px; color: var(--heading); letter-spacing: .3px; height: 26px; }
  .service-photo { width: 207px; height: 115px; border: 1px solid #555; }
  .service p { margin-top: 9px; font-size: 11px; line-height: 14px; color: var(--text-muted); }
  .read-more { display: block; margin-top: 10px; margin-left: 4px; font-size: 11px; color: var(--link-blue); text-decoration: none; }

  .welcome {
    position: absolute; left: 0; top: 868px; width: 1123px; height: 199px;
    background: linear-gradient(#1b1b1b, #303030);
  }
  .welcome h1 {
    position: absolute; left: 112px; top: 19px; font-weight: 400; font-size: 17px; color: var(--heading);
    padding-bottom: 6px; border-bottom: 1px dotted #bbbbbb; width: 162px;
  }
  .welcome h1 span { color: var(--brand-blue); }
  .welcome p { position: absolute; left: 112px; top: 65px; width: 890px; font-size: 13px; line-height: 21px; color: var(--text-light); }
  .welcome .read-more { position: absolute; left: 111px; top: 160px; margin: 0; }

  .site-footer { position: absolute; left: 0; top: 1067px; width: 1123px; height: 133px; background: var(--footer-bg); }
  .social { position: absolute; left: 115px; top: 31px; display: flex; gap: 6px; }
  .social span { width: 30px; height: 30px; border-radius: 5px; background: linear-gradient(#3f8fd6, #1a5fa3); }
  .social .rss { background: linear-gradient(#f6a04a, #e0661b); }
  .footer-nav { position: absolute; left: 441px; top: 29px; font-size: 12px; color: var(--text-light); word-spacing: 1px; }
  .footer-nav .sep { margin: 0 11px; }
  .copyright { position: absolute; left: 535px; top: 67px; font-size: 12px; color: var(--white); }
</style>
</head>
<body>
  <div class="top-strip"></div>
  <div class="header-zone"></div>

  <header class="masthead">
    <div class="brand-mark">KVT</div>
    <div class="brand-name">Torvello &amp; Associates, LLC</div>
    <div class="brand-tagline">Intellectual Property and Cyber Security</div>
    <div class="search-field">Search</div>
    <div class="search-go">Go</div>
  </header>

  <nav class="main-nav">
    <a class="is-active" href="#">HOME</a>
    <a style="left:132px" href="#">ABOUT KVT</a>
    <a style="left:264px" href="#">PRACTICE AREAS</a>
    <a style="left:435px" href="#">ASSOCIATES</a>
    <a style="left:575px" href="#">CONTACT US</a>
  </nav>

  <section class="hero-frame">
    <div class="hero-photo" role="img" aria-label="Photo of colleagues meeting at a conference table in front of a screen showing a bar chart"></div>
    <div class="hero-dots"><span class="is-current"></span><span></span><span></span><span></span></div>
  </section>

  <section class="service" style="left:88px">
    <h2>CYBER SECURITY</h2>
    <div class="service-photo" role="img" aria-label="Image of a glowing blue globe with a network cable" style="background:linear-gradient(135deg,#0d2d55,#2a72b5 60%,#103a66)"></div>
    <p>Nunc varius facilisis eros. Sed erat. In in velit quis arcu ornare laoreet. luctus massa.Integer ut purus ac augue &nbsp;commodo.</p>
    <a class="read-more" href="#">Read More &nbsp;&gt;&gt;</a>
  </section>

  <section class="service" style="left:331px">
    <h2>GENERAL INVESTIGATIONS</h2>
    <div class="service-photo" role="img" aria-label="Photo of hands typing on a keyboard in blue light" style="background:linear-gradient(135deg,#7fc6e4,#2f8fbf 55%,#1b4f70)"></div>
    <p>Nunc varius facilisis eros. Sed erat. In in velit quis arcu ornare laoreet. luctus massa.Integer ut purus ac augue &nbsp;commodo.</p>
    <a class="read-more" href="#">Read More &nbsp;&gt;&gt;</a>
  </section>

  <section class="service" style="left:574px">
    <h2>DATA PROTECTION</h2>
    <div class="service-photo" role="img" aria-label="Photo of a laptop secured on a white background" style="background:linear-gradient(180deg,#ffffff,#e4e1dc 60%,#b7a98f)"></div>
    <p>Nunc varius facilisis eros. Sed erat. In in velit quis arcu ornare laoreet. luctus massa.Integer ut purus ac augue &nbsp;commodo.</p>
    <a class="read-more" href="#">Read More &nbsp;&gt;&gt;</a>
  </section>

  <section class="service" style="left:821px">
    <h2>PHYSICAL SECURITY SERVICES</h2>
    <div class="service-photo" role="img" aria-label="Close-up photo of a finger pressing a key on a dark keyboard" style="background:linear-gradient(135deg,#3a3d44,#6c7079 55%,#2b2d32)"></div>
    <p>Nunc varius facilisis eros. Sed erat. In in velit quis arcu ornare laoreet. luctus massa.Integer ut purus ac augue &nbsp;commodo.</p>
    <a class="read-more" href="#">Read More &nbsp;&gt;&gt;</a>
  </section>

  <section class="welcome">
    <h1>WELCOME TO <span>KVT</span></h1>
    <p>Nunc varius facilisis eros. Sed erat. In in velit quis arcu ornare laoreet. Curabitur adipiscing luctus massa.Integer ut purus ac augue commodo commodo. Nunc nec mi eu justo tempor consectetuer. Etiam vitae nisl. In dignissim lacus ut ante. Cras elit lectus, bibendum a, adipiscing vitae, commodo et, dui. Lorem ipsum dolor sit amet, consectetuer adipiscing elit. Nam nibh. Nunc varius facilisis eros. Sed erat. In in velit quis arcu ornare laoreet. Curabitur adipiscing luctus massa.</p>
    <a class="read-more" href="#">Read More &nbsp;&gt;&gt;</a>
  </section>

  <footer class="site-footer">
    <div class="social" aria-label="Social links">
      <span></span><span></span><span></span><span class="rss"></span>
    </div>
    <div class="footer-nav">Home<span class="sep">|</span>About KVT<span class="sep">|</span>Practice Areas<span class="sep">|</span>Associates<span class="sep">|</span>Contact us</div>
    <div class="copyright">Copyright 2011 KVT, All Rights Reserved</div>
  </footer>
</body>
</html>
```